Sunset Harbor Living Web Page

We need a web page design that has two intro pages - first being a 'home page', then a link to the second page that has the 'content tabs' and a 'call to action' (see below).

The business helps people that wish to retire to S.E.Asia (Thailand, Malaysia, Indonesia,The Philippines etc) - to enjoy the lifestyle and the remaining years of their lives. What attracts S.E.Asia to many people is the lower cost, the atmoshpere and beauty of the tropics and the vibrancy of the various countries.

People that are wishing to make the most of their retirement and are adventurous at a great bargain compared to the cost of their own countries will be interested.

We help them achieve this - visa, financials (tax, gov't payments etc), introduce them to the right people for property, clubs, retirement facilities, insurance and so forth.

Therefore we are providing an extremely wide ranging service and this site will provide broad but general information only - with a call to action to come and see us for more specific information and how we can help them specifically.

This site will be predominantly for travel and lifestyle, it will be linked with another financial services (financial planning) site later down the track.

The colour scheme is dark green and blue - as per the attached logo design. Photos and background just think lifestyle and S.E.Asia - beaches/mountains/water/recreational activities for retirees.

Target market is mostly those coming up to retirement to those that are already retired. But we also expect to have some interest with younger people that would like to find out more and plan for the future. So a broad age group but I would say mostly 40-70 yrs old.

On the first (Home) page we would like our company name 'Sunset Harbor Living', our logo (which will be on all pages) and a statement such as: “Imagine a retirement where your dreams are brought to life, and you have never felt more alive. Let us show you how”. Then a link to the second page.

We would like an uncluttered site. On the second (contents) page the tabs would be:

- Visa
- Property
- Financials
- Travel
- Insurance & Healthcare
- Medical Tourism
- Cost of living
- Weekly Blogs and articles
- Sunset Harbor Living story

We would also like a call to action on the second page - asking them to leave their contact details if they wish to learn more or sign up to our weekly newsletter/blog.

We are open to suggestions and your imaginations.

Thank you
Malcolm

Font styles to use
Serif
Script

Colors
0255a3
3377b5
00a990
9bcb3c
abd036
33b8a4
85abd2
cadf82
86cfc6

Requirements
Must have
• I have been asked by the web designer to receive a 'Web Font' so that we can 'get off of Zentrofy'. Hope that makes sense.

```html
<!DOCTYPE html>
<html lang="en">
<head>
<meta charset="utf-8">
<title>Sunset Harbor Living – Home</title>
<link href="https://fonts.googleapis.com/css2?family=Roboto+Condensed:wght@400;700&display=swap" rel="stylesheet">
<style>
:root{
  --brand-green:#00a990;
  --brand-blue:#0255a3;
  --sky:#00b2ea;
  --sky-deep:#0078c4;
  --lime:#abd036;
  --lime-ring:#d6e99a;
  --grey-text:#7a7a7a;
  --white:#ffffff;
  --footer-bg:#111111;
  --footer-text:#9a9a9a;
}
*{margin:0;padding:0;box-sizing:border-box}
html,body{width:1200px;height:686px;overflow:hidden;background:var(--white)}
body{font-family:"Roboto Condensed",Arial,sans-serif;position:relative}
.top-strip{position:absolute;left:0;top:0;width:1200px;height:4px;background:linear-gradient(90deg,var(--brand-green),var(--sky))}
.site-header{position:absolute;left:0;top:4px;width:1200px;height:97px;background:var(--white)}
.brand{position:absolute;left:99px;top:24px;display:flex;align-items:center;gap:8px}
.brand-mark{width:34px;height:34px;border-radius:50%;background:var(--brand-green)}
.brand-name{font-size:20px;font-weight:700;color:var(--brand-blue);line-height:1}
.contact{position:absolute;top:25px;display:flex;align-items:center}
.contact-phone{left:676px}
.contact-mail{left:892px}
.contact-icon{width:44px;height:44px;border-radius:50%;background:var(--lime);border:3px solid var(--lime-ring);display:flex;align-items:center;justify-content:center}
.contact-text{margin-left:23px;font-size:14px;line-height:21px;color:var(--grey-text)}
.main-nav{position:absolute;left:0;top:101px;width:1200px;height:58px;background:linear-gradient(180deg,var(--sky),var(--sky-deep));border-bottom:2px solid var(--brand-green)}
.main-nav ul{list-style:none;display:flex;gap:22px;position:absolute;left:99px;top:19px}
.main-nav li{font-size:14.5px;color:var(--white);white-space:nowrap}
.nav-marker{position:absolute;left:111px;bottom:-2px;width:0;height:0;border-left:5px solid transparent;border-right:5px solid transparent;border-bottom:6px solid var(--brand-green)}
.hero{position:absolute;left:0;top:159px;width:1200px;height:464px;background:
  radial-gradient(ellipse 60% 50% at 30% 10%,rgba(150,140,120,.55),transparent 70%),
  linear-gradient(180deg,#6b6558 0%,#3b362d 35%,#2a2620 60%,#4a3c22 85%,#5e4a22 100%)}
.hero-headline{position:absolute;left:0;top:135px;width:1200px;text-align:center;color:var(--white);font-size:32px;font-weight:700;line-height:52px;text-transform:uppercase;text-shadow:1px 2px 3px rgba(0,0,0,.6)}
.hero-cta{position:absolute;left:454px;top:275px;width:274px;height:48px;border:2px solid var(--white);border-radius:24px;color:var(--white);font-size:23px;text-align:center;line-height:44px}
.slider-arrow{position:absolute;top:212px;width:40px;height:40px}
.slider-prev{left:38px}
.slider-next{left:1127px}
.site-footer{position:absolute;left:0;top:623px;width:1200px;height:63px;background:var(--footer-bg);color:var(--footer-text);font-size:12px}
.footer-legal{position:absolute;left:52px;top:24px}
.footer-legal span{margin:0 7px}
.footer-social{position:absolute;left:815px;top:25px;display:flex;align-items:center}
.social-dot{width:8px;height:8px;border-radius:50%;background:var(--footer-text);margin-left:26px}
.social-dot:first-child{margin-left:14px}
</style>
</head>
<body>
<div class="top-strip"></div>
<header class="site-header">
  <div class="brand"><div class="brand-mark"></div><div class="brand-name">Sunset Harbor Living</div></div>
  <div class="contact contact-phone">
    <div class="contact-icon"><svg width="18" height="18" viewBox="0 0 24 24"><path fill="#fff" d="M6.6 10.8a15.1 15.1 0 0 0 6.6 6.6l2.2-2.2a1 1 0 0 1 1-.25 11.4 11.4 0 0 0 3.6.57 1 1 0 0 1 1 1V20a1 1 0 0 1-1 1A17 17 0 0 1 3 4a1 1 0 0 1 1-1h3.5a1 1 0 0 1 1 1c0 1.25.2 2.45.57 3.57a1 1 0 0 1-.25 1z"/></svg></div>
    <div class="contact-text">CALL US ON :<br>(055) - 3124789650</div>
  </div>
  <div class="contact contact-mail">
    <div class="contact-icon"><svg width="20" height="16" viewBox="0 0 20 16"><rect x="1" y="1" width="18" height="14" rx="2" fill="none" stroke="#fff" stroke-width="2"/><path d="M2 3l8 6 8-6" fill="none" stroke="#fff" stroke-width="2"/></svg></div>
    <div class="contact-text">MAIL US ON :<br>info@sunsetharborliving.com</div>
  </div>
</header>
<nav class="main-nav">
  <ul>
    <li>Home</li><li>Visa</li><li>Property</li><li>Financials</li><li>Travel</li><li>Insurance &amp; Healthcare</li><li>Medical Tourism</li><li>Cost of living</li><li>Weekly Blogs and articles</li><li>Sunset Harbor Living story</li><li>Contact us</li>
  </ul>
  <div class="nav-marker"></div>
</nav>
<section class="hero" role="img" aria-label="Photograph of sunlit mountain ridges at dusk">
  <h1 class="hero-headline">Imagine a retirement where your dreams are<br>brought to life, and you have never felt more alive</h1>
  <div class="hero-cta">Let us show you how</div>
  <svg class="slider-arrow slider-prev" viewBox="0 0 40 40"><circle cx="20" cy="20" r="18.5" fill="none" stroke="rgba(255,255,255,.6)" stroke-width="2"/><path d="M11 20l14-9v18z" fill="rgba(255,255,255,.6)"/></svg>
  <svg class="slider-arrow slider-next" viewBox="0 0 40 40"><circle cx="20" cy="20" r="18.5" fill="none" stroke="rgba(255,255,255,.6)" stroke-width="2"/><path d="M29 20l-14-9v18z" fill="rgba(255,255,255,.6)"/></svg>
</section>
<footer class="site-footer">
  <div class="footer-legal">© 2016 Company Name . all rights reserved<span>/</span>Terms and Conditions<span>/</span>Privacy policy</div>
  <div class="footer-social">Connect with our social network :<div class="social-dot"></div><div class="social-dot"></div><div class="social-dot"></div><div class="social-dot"></div></div>
</footer>
</body>
</html>
```